IT Company requires new Business Card design.

Over the years we have had a few different business card designs. We are now due for new cards across the board for all staff. We felt this would be a good time to start fresh with a new design. Our traditional card simply had our details on the front, and a list of services on the back. We don't particularly need the list of services, we have had cards where the only thing on the rear of the card was our logo.
Feel free to be creative, we would like our tag line "Complete IT Management" to appear at some point, doesn't necessarily have to be with the logo.
I have attached samples and drafts of various previous cards we have used over the years.

```html
<!DOCTYPE html>
<html lang="en">
<head>
<meta charset="utf-8">
<title>Harbor Systems — Business Card</title>
<link rel="stylesheet" href="https://fonts.googleapis.com/css2?family=Source+Sans+3:wght@400;600;700&display=swap">
<style>
  :root {
    --backdrop: #e8e6e3;
    --card-white: #ffffff;
    --slate: #5f6e7a;
    --slate-dark: #3f4a53;
    --ink: #4a4f54;
    --brand: #5f6e7a;
    --light: #ffffff;
  }
  * { margin: 0; padding: 0; box-sizing: border-box; }
  html, body {
    width: 1034px; height: 1200px; overflow: hidden;
    background: var(--backdrop);
    font-family: "Source Sans 3", "Myriad Pro", Arial, sans-serif;
  }
  .canvas { position: relative; width: 1034px; height: 1200px; }

  .card {
    position: absolute; left: 75px; width: 899px; height: 511px;
    border-radius: 34px; overflow: hidden;
  }
  .card--front { top: 69px; background: var(--card-white); }
  .card--back  { top: 626px; background: var(--slate); }

  .card__wave { position: absolute; inset: 0; width: 100%; height: 100%; }

  .brand {
    position: absolute; display: flex; align-items: center; gap: 26px;
    color: var(--brand); font-weight: 700; line-height: 0.9;
    text-transform: uppercase;
  }
  .brand__square { background: currentColor; flex: none; }
  .brand__name span { display: block; }

  .card--front .brand { left: 182px; top: 45px; }
  .card--front .brand__square { width: 128px; height: 128px; }
  .card--front .brand__name { font-size: 74px; letter-spacing: -1px; }
  .card--front .brand__name span + span { font-size: 52px; letter-spacing: 0.5px; margin-top: 8px; }

  .address {
    position: absolute; top: 254px; left: 0; width: 100%;
    text-align: center; font-size: 22px; color: var(--ink);
  }

  .person { position: absolute; left: 79px; top: 430px; color: var(--light); }
  .person__name { font-size: 28px; font-weight: 700; line-height: 1.1; }
  .person__role { font-size: 22px; font-weight: 400; margin-top: 4px; }

  .contacts {
    position: absolute; right: 84px; top: 354px;
    list-style: none; color: var(--light); font-size: 22px;
  }
  .contacts li {
    display: flex; align-items: center; justify-content: flex-end;
    gap: 8px; height: 35.5px;
  }
  .contacts svg { width: 20px; height: 20px; fill: var(--light); }

  .card--back .brand {
    left: 0; right: 0; top: 118px; justify-content: center;
    color: var(--light);
  }
  .card--back .brand__square { width: 170px; height: 170px; }
  .card--back .brand__name { font-size: 92px; }
  .card--back .brand__name span + span { font-size: 64px; margin-top: 10px; }

  .tagline {
    position: absolute; left: 0; right: 0; top: 452px;
    text-align: center; color: var(--light);
    font-size: 23px; letter-spacing: 5px; font-weight: 400;
  }
</style>
</head>
<body>
<main class="canvas">

  <section class="card card--front" aria-label="Business card front">
    <svg class="card__wave" viewBox="0 0 899 511" preserveAspectRatio="none" aria-hidden="true">
      <path d="M0,232 C140,372 430,400 899,282 L899,511 L0,511 Z" fill="var(--slate)"/>
      <path d="M0,222 C140,360 430,390 899,270" fill="none" stroke="var(--slate-dark)" stroke-width="7"/>
      <path d="M0,210 C150,352 440,378 899,256" fill="none" stroke="var(--slate-dark)" stroke-width="3"/>
      <path d="M0,240 C140,380 430,408 899,290" fill="none" stroke="#ffffff" stroke-width="3" opacity="0.6"/>
    </svg>

    <div class="brand">
      <div class="brand__square"></div>
      <div class="brand__name"><span>Harbor</span><span>Systems</span></div>
    </div>

    <p class="address">Unit 4 18 Marlow Street, Ferndale WA 6148</p>

    <div class="person">
      <p class="person__name">Daniel Reeve</p>
      <p class="person__role">Operations Manager</p>
    </div>

    <ul class="contacts">
      <li>
        <svg viewBox="0 0 20 20" aria-hidden="true"><circle cx="10" cy="10" r="9" fill="none" stroke="#fff" stroke-width="1.6"/><path d="M7 5.5l1.8 2.2-1 1.2c.6 1.3 1.6 2.3 2.8 2.9l1.2-1 2.2 1.8-1.2 1.8c-3.6-.4-6.8-3.6-7.2-7.2z"/></svg>
        <span>08 9312 4860</span>
      </li>
      <li>
        <svg viewBox="0 0 20 20" aria-hidden="true"><rect x="5" y="1" width="10" height="18" rx="2"/><rect x="7" y="4" width="6" height="6" fill="var(--slate)"/></svg>
        <span>0412 583 907</span>
      </li>
      <li>
        <svg viewBox="0 0 20 20" aria-hidden="true"><rect x="5" y="2" width="10" height="6"/><rect x="1" y="8" width="18" height="9" rx="2"/><rect x="5" y="11" width="10" height="2" fill="var(--slate)"/></svg>
        <span>08 9312 4860</span>
      </li>
      <li>
        <svg viewBox="0 0 20 20" aria-hidden="true"><path d="M2 8l8-5 8 5v9H2z"/><path d="M3 8l7 5 7-5" fill="none" stroke="var(--slate)" stroke-width="1.6"/></svg>
        <span>daniel@harborsystems.com.au</span>
      </li>
    </ul>
  </section>

  <section class="card card--back" aria-label="Business card back">
    <div class="brand">
      <div class="brand__square"></div>
      <div class="brand__name"><span>Harbor</span><span>Systems</span></div>
    </div>
    <p class="tagline">COMPLETE IT MANAGEMENT</p>
  </section>

</main>
</body>
</html>
```